Velvet Meadow Hamper company needs a brochure design

We need a brochure design for a new company in Dubai called 'Velvet Meadow Hampers'. We already have a logo designed which I have attached and would like to use this and the green/gold/white colours for our brochure. Our company initially will be supplying Velvet Meadow Hamper wear of traditional wicker baskets in many designs which hold all the cutlery, crockery and accessories. We will also be selling picnic accessories. We want to purvey a sense of luxury and class in line with our logo. I have attached some photos of the picnicwear. As our products are changing all the time I thought a fold out cover which stays the same and then product cards inserted into the folder which can be changed according to our product changes. I am looking for a fairly simple design and each product card should have at least one photo of the product on it with a spec and description also. On the cover of the folder I would like room to write about the company and what we do, this can be inside or out and may or may not include photos. I have the logo designs in illustrator format and pdf. Please contact if any more information is needed.
Updates

Reason: I have extended this deadline as there are some content changes taking place.

Industry/Entity Type

It Company

```html
<!DOCTYPE html>
<html lang="en">
<head>
<meta charset="utf-8">
<title>Velvet Meadow Hampers – Harbourlight Product Card</title>
<link rel="stylesheet" href="https://fonts.googleapis.com/css2?family=Montserrat:wght@600&family=Merriweather:wght@300;400&display=swap">
<style>
  :root {
    --forest: #1b321d;
    --forest-deep: #172b19;
    --gold: #d3a33a;
    --gold-soft: #c9a45a;
    --cream: #f4efe4;
    --paper: #ffffff;
    --taupe: #9c8a72;
    --band-dark: #6b2a14;
  }
  * { box-sizing: border-box; margin: 0; padding: 0; }
  html, body { width: 1200px; height: 1000px; overflow: hidden; background: var(--paper); }
  body { position: relative; font-family: "Merriweather", Georgia, serif; }

  .card {
    position: absolute; top: 150px; width: 493px; height: 700px;
    background: var(--forest); overflow: hidden;
  }
  .card--front { left: 100px; }
  .card--spec { left: 607px; }

  /* Front card */
  .brand-header { position: absolute; left: 0; top: 0; width: 100%; height: 147px; }
  .brand-name {
    position: absolute; left: 0; right: 0; top: 64px; text-align: center;
    font-family: "Montserrat", Arial, sans-serif; font-weight: 600;
    font-size: 12.5px; letter-spacing: 2.2px; color: var(--gold);
  }
  .brand-name .brand-dot {
    display: inline-block; width: 7px; height: 7px; border-radius: 50%;
    background: var(--gold); margin-right: 10px; vertical-align: 1px;
  }
  .gilt-band {
    position: absolute; left: 0; width: 100%; height: 6px;
    background: linear-gradient(90deg, var(--band-dark) 0%, #a8641f 30%, #e8c98a 55%, #fffaf0 72%, #d9a53c 85%, var(--band-dark) 100%);
  }
  .gilt-band--top { top: 147px; }
  .gilt-band--bottom { top: 513px; }
  .product-stage { position: absolute; left: 0; top: 153px; width: 100%; height: 360px; background: var(--paper); }
  .product-photo {
    position: absolute; left: 32px; top: 34px; width: 430px; height: 296px;
    background: radial-gradient(ellipse at 50% 55%, #a89378 0%, #bfb09a 45%, #ffffff 75%);
  }
  .product-title {
    position: absolute; left: 28px; top: 536px;
    font-family: "Montserrat", Arial, sans-serif; font-weight: 600;
    font-size: 22px; letter-spacing: 3px; color: var(--gold);
  }
  .product-intro {
    position: absolute; left: 28px; top: 572px; width: 420px;
    font-size: 9.6px; line-height: 12.4px; color: var(--cream); font-weight: 300;
  }
  .corner-flourish {
    position: absolute; left: 455px; top: 585px; width: 38px; height: 80px;
    background: linear-gradient(180deg, rgba(255,255,255,0.05), rgba(255,255,255,0.02));
    border-radius: 20px 0 0 20px;
  }
  .site-url {
    position: absolute; left: 0; right: 0; top: 673px; text-align: center;
    font-size: 9.6px; color: var(--gold-soft);
  }

  /* Spec card */
  .divider { position: absolute; left: 179px; width: 135px; height: 1px; background: var(--gold); }
  .divider--top { top: 188px; }
  .divider--bottom { top: 512px; }
  .flourish {
    position: absolute; left: 219px; width: 56px; height: 16px;
    background: rgba(211,163,58,0.55); border-radius: 8px;
  }
  .flourish--top { top: 168px; }
  .flourish--bottom { top: 516px; }
  .spec-title {
    position: absolute; left: 0; right: 0; top: 210px; text-align: center;
    font-family: "Montserrat", Arial, sans-serif; font-weight: 600;
    font-size: 21px; letter-spacing: 3px; color: var(--gold);
  }
  .spec-subtitle {
    position: absolute; left: 0; right: 0; top: 238px; text-align: center;
    font-size: 14px; color: var(--gold); letter-spacing: 0.3px;
  }
  .spec-list {
    position: absolute; left: 112px; top: 276px; list-style: none;
    font-size: 10.4px; line-height: 16.4px; color: var(--cream);
  }
  .spec-list li { position: relative; padding-left: 14px; }
  .spec-list li::before {
    content: ""; position: absolute; left: 0; top: 6px; width: 5px; height: 5px;
    background: var(--gold);
  }
</style>
</head>
<body>

<section class="card card--front">
  <header class="brand-header">
    <div class="brand-name"><span class="brand-dot"></span>VELVET MEADOW HAMPERS</div>
  </header>
  <div class="gilt-band gilt-band--top"></div>
  <div class="product-stage">
    <div class="product-photo" role="img" aria-label="Photo of the Harbourlight antique wash willow picnic basket with both lids open, showing plates and cutlery"></div>
  </div>
  <div class="gilt-band gilt-band--bottom"></div>
  <h1 class="product-title">HARBOURLIGHT</h1>
  <p class="product-intro">This beautiful hand crafted basket has a classic double lidded design with an antique wash, perfect for those wanting to embrace the bygone era of picnicking. Inside the basket is adorned with beautifully tailored taupe fabrics and contains place settings for four people, including napkins, fresh white plates, stainless steel cutlery and wine glasses, while the built in chiller compartment, keeps food ready to consume. Great for those lazy days in the sunshine!</p>
  <div class="corner-flourish" role="img" aria-label="Faint decorative flourish"></div>
  <p class="site-url">www.velvetmeadowhampers.com</p>
</section>

<section class="card card--spec">
  <div class="flourish flourish--top" role="img" aria-label="Gold ornamental flourish"></div>
  <div class="divider divider--top"></div>
  <h2 class="spec-title">HARBOURLIGHT</h2>
  <p class="spec-subtitle">OVERVIEW</p>
  <ul class="spec-list">
    <li>Handmade antique wash willow basket for four people</li>
    <li>Classic double lidded design</li>
    <li>Cream leather straps and trim</li>
    <li>Built in chiller compartment</li>
    <li>Contemporary light taupe colour palette</li>
    <li>4 White china plates</li>
    <li>4 Stainless steel, knifes, forks and spoons</li>
    <li>Stainless steel salt and pepper mills</li>
    <li>1 Stainless steel waiters friend bottle opener</li>
    <li>4 taupe napkins</li>
    <li>4 wine glasses</li>
    <li>Hamper dimensions 480 x 330 x 280mm<br>(400mm with handle)</li>
  </ul>
  <div class="divider divider--bottom"></div>
  <div class="flourish flourish--bottom" role="img" aria-label="Gold ornamental flourish"></div>
  <p class="site-url">www.velvetmeadowhampers.com</p>
</section>

</body>
</html>
```